Website Design for Employee Moral and Happiness Company

Looking for a clean website design that explains our features in a step by step manner so our visitors know exactly what our site does before logging in.

The site is called "Velrato". See logo design and video for a sample of style and an overview of what we do.

Target Market(s)

Business owners that are looking to retain employees.

Number of Pages Required

1 page

```html
<!DOCTYPE html>
<html lang="en">
<head>
<meta charset="utf-8">
<title>Velrato — Employee Morale and Happiness</title>
<link href="https://fonts.googleapis.com/css2?family=Noto+Serif:wght@700&family=Roboto:ital,wght@0,400;0,500;0,700;1,400&display=swap" rel="stylesheet">
<style>
:root{
  --orange:#f2561d;
  --orange-soft:#f9b59a;
  --dark:#141619;
  --ink:#1d1d1f;
  --grey:#6f6f73;
  --line:#d9d9dc;
  --white:#ffffff;
}
*{box-sizing:border-box;margin:0;padding:0}
html,body{width:1200px;height:4030px;overflow:hidden;background:var(--white)}
body{position:relative;font-family:"Roboto",Arial,sans-serif;color:var(--ink)}
.abs{position:absolute}
.serif{font-family:"Noto Serif",Georgia,serif;font-weight:700}
.accent{color:var(--orange)}
.btn{position:absolute;display:flex;align-items:center;justify-content:center;gap:8px;background:var(--orange);color:var(--white);border-radius:26px;font-weight:700;font-size:15px;letter-spacing:.2px}

/* header */
.topbar{left:0;top:0;width:1200px;height:5px;background:var(--orange)}
.brand{font-family:"Noto Serif",Georgia,serif;font-weight:700;font-size:54px;letter-spacing:-1px}
.site-header .brand{left:110px;top:10px;color:var(--ink)}
.nav{left:0;top:44px;font-size:14.5px;font-weight:700}
.nav span{position:absolute;white-space:nowrap}
.nav .active{color:var(--orange)}
.login{left:959px;top:28px;width:128px;height:50px}

/* hero */
.hero{left:0;top:103px;width:1200px;height:632px;background:linear-gradient(100deg,#eef0f2 0%,#d7dde2 45%,#9aa6b2 75%,#6f7f90 100%)}
.hero-rule{left:112px;top:253px;width:5px;height:237px;background:var(--orange)}
.hero-title{left:138px;top:270px;font-size:45px;line-height:60px;white-space:nowrap;color:var(--ink)}
.hero-sub{left:138px;top:336px;font-size:17.5px;font-weight:500;line-height:28px;color:#25272b}
.started{left:138px;top:413px;width:155px;height:49px}
.social-ring{position:absolute;left:1121px;width:36px;height:36px;border:2px solid var(--white);border-radius:50%}
.hero-dots{left:564px;top:659px;display:flex;gap:6px}
.hero-dots i{width:13px;height:13px;border-radius:50%;background:var(--white);border:2px solid #c9ced3}

/* about */
.about-ring{left:110px;top:791px;width:430px;height:415px;border-radius:50%;background:var(--orange)}
.about-photo{left:118px;top:789px;width:428px;height:418px;border-radius:50%;background:radial-gradient(circle at 40% 40%,#e8d6c6,#b79a86 55%,#4f5566)}
.about h2{left:598px;top:822px;font-size:35px;white-space:nowrap}
.about p{position:absolute;left:598px;width:492px;font-size:14px;line-height:25.5px;color:var(--grey)}
.learn{left:598px;top:1119px;width:144px;height:47px}

/* video + features */
.feature-bg{left:0;top:0}
.video-frame{left:192px;top:1284px;width:814px;height:446px;background:var(--white);padding:8px;box-shadow:0 10px 30px rgba(0,0,0,.25)}
.video-art{width:100%;height:100%;background:linear-gradient(180deg,#ddd5c4 0%,#d9d1bf 55%,#9f9f9c 56%,#8f908f 100%)}
.features h2{left:0;width:1200px;top:1780px;text-align:center;color:var(--white);font-size:40px}
.features-lead{left:165px;width:870px;top:1852px;text-align:center;color:var(--white);font-size:14.5px;line-height:26px}
.feature-card{position:absolute;top:1951px;width:308px;height:313px;background:var(--white);border-radius:5px;text-align:center}
.feature-card svg{position:absolute;left:121px;top:28px}
.feature-card h3{position:absolute;left:0;width:100%;top:118px;font-size:19.5px;font-weight:700;line-height:27px}
.feature-card p{position:absolute;left:20px;width:268px;top:186px;font-size:14px;line-height:25.5px;color:var(--grey)}

/* testimonials */
.section-title{left:0;width:1200px;text-align:center;font-size:33px}
.quote-text{position:absolute;top:2499px;width:440px;font-size:14px;font-style:italic;line-height:24.5px;color:#8b8b90}
.t-divider{left:599px;top:2520px;width:1px;height:120px;background:var(--line)}
.avatar{position:absolute;top:2591px;width:56px;height:56px;border-radius:50%;background:linear-gradient(160deg,#c7ccd2,#7d858f)}
.t-name{position:absolute;top:2598px;font-size:14.5px;font-weight:700;white-space:nowrap}
.t-name small{font-size:13px;font-weight:400;color:var(--grey)}
.stars{position:absolute;top:2618px;color:var(--orange);font-size:12px;letter-spacing:1px}
.qmark{position:absolute;top:2568px;font-family:"Noto Serif",Georgia,serif;font-size:110px;line-height:1;color:var(--orange-soft)}
.t-dots{left:571px;top:2688px;display:flex;gap:6px}
.t-dots i{width:10px;height:10px;border-radius:50%;background:#c6c6c9}
.t-dots i.on{background:var(--orange)}

/* trusted */
.trusted{left:0;top:2788px;width:1200px;height:307px;background:var(--orange)}
.partner{position:absolute;top:2941px;width:177px;height:86px;background:var(--white);border-radius:4px;box-shadow:0 4px 10px rgba(0,0,0,.12)}
.partner i{position:absolute;left:58px;top:20px;width:60px;height:46px;border-radius:6px;background:#e4e4e7}
.arrow{position:absolute;top:2968px}

/* blog */
.blog-card{position:absolute;top:3251px;width:308px;height:394px;background:var(--white);box-shadow:0 2px 12px rgba(0,0,0,.13)}
.blog-img{position:absolute;left:8px;top:8px;width:292px;height:191px}
.blog-date{position:absolute;left:11px;top:218px;font-size:14px;color:var(--grey);display:flex;align-items:center;gap:9px}
.blog-card h3{position:absolute;left:11px;top:247px;width:290px;font-size:15.5px;font-weight:700;line-height:24px}
.blog-card p{position:absolute;left:11px;top:301px;width:290px;font-size:13px;line-height:23px;color:var(--grey)}
.read{position:absolute;left:11px;top:355px;font-size:13.5px;font-weight:700;color:var(--orange);display:flex;align-items:center;gap:8px}

/* footer */
.footer{left:0;top:3736px;width:1200px;height:294px;background:var(--dark);color:var(--white)}
.footer-brand{left:110px;top:3781px;color:var(--white);font-size:60px}
.f-social{position:absolute;top:3889px;width:34px;height:34px;border-radius:50%;background:var(--orange);border:2px solid var(--white)}
.f-head{position:absolute;top:3791px;font-size:15px;font-weight:700;color:var(--white);letter-spacing:.2px}
.f-link{position:absolute;font-size:14px;color:#e6e6e6;display:flex;align-items:center;gap:14px;white-space:nowrap}
.f-link b{width:12px;height:12px;border-radius:50%;background:var(--orange);position:relative}
.f-link b::after{content:"";position:absolute;left:3px;top:3.5px;border-left:5px solid var(--white);border-top:2.5px solid transparent;border-bottom:2.5px solid transparent}
.c-icon{position:absolute;left:867px;width:34px;height:34px;border-radius:50%;background:var(--orange);display:flex;align-items:center;justify-content:center}
.c-text{position:absolute;left:923px;font-size:14px;line-height:23px;color:#e6e6e6}
.f-rule{left:111px;top:3978px;width:978px;height:1px;background:#5a5c61}
.copy{left:0;width:1200px;top:3993px;text-align:center;font-size:13px;color:#e6e6e6}
</style>
</head>
<body>

<!-- header -->
<div class="abs topbar"></div>
<header class="site-header">
  <div class="abs brand">velrato</div>
  <nav class="abs nav">
    <span class="active" style="left:460px">HOME</span>
    <span style="left:535px">ABOUT</span>
    <span style="left:615px">FEATURES</span>
    <span style="left:720px">BLOG</span>
    <span style="left:790px">CONTACT</span>
  </nav>
  <div class="btn login">
    <svg width="16" height="16" viewBox="0 0 16 16"><circle cx="8" cy="8" r="7" fill="none" stroke="#fff" stroke-width="1.6"/><circle cx="8" cy="6.3" r="2.4" fill="#fff"/><path d="M3.6 12.6c1-2 2.6-2.8 4.4-2.8s3.4.8 4.4 2.8" fill="#fff"/></svg>
    LOGIN
  </div>
</header>

<!-- hero -->
<section class="abs hero" role="img" aria-label="Smiling businessman in a blue suit holding a tablet in a bright office with colleagues working behind him"></section>
<svg class="abs" style="left:0;top:560px" width="1200" height="180" viewBox="0 0 1200 180">
  <path d="M0 40 C300 180 800 210 1200 30 L1200 180 L0 180Z" fill="#fff"/>
  <path d="M0 40 C300 170 800 195 1200 30" fill="none" stroke="#9aa2ab" stroke-width="4"/>
  <path d="M0 48 C300 196 800 214 1200 36" fill="none" stroke="#2b2f35" stroke-width="5"/>
</svg>
<div class="abs hero-rule"></div>
<h1 class="abs hero-title serif">WELCOME TO <span class="accent">VELRATO</span></h1>
<p class="abs hero-sub">Lorem ipsum dolor sit amet, consectetur adipiscing elit<br>sed do eiusmod tempor incididuntea.</p>
<div class="btn started">GET STARTED</div>
<i class="social-ring" style="top:287px"></i>
<i class="social-ring" style="top:332px"></i>
<i class="social-ring" style="top:376px"></i>
<i class="social-ring" style="top:422px"></i>
<div class="abs hero-dots"><i></i><i></i><i></i><i></i></div>

<!-- about -->
<section class="about">
  <div class="abs about-ring"></div>
  <div class="abs about-photo" role="img" aria-label="Two smiling women in a meeting with a colleague at an office table"></div>
  <h2 class="abs serif">ABOUT <span class="accent">VELRATO</span></h2>
  <p style="top:888px">Sed ut perspiciatis unde omnis iste natus error sit voluptatem accusantium doloremque laudantium, totam rem aperiam, eaque ipsa quae ab illo inven tore veritatis et quasi architecto beatae vitae dicta sunt explicabo nemo enim ipsam voluptatem quia voluptasea.</p>
  <p style="top:1007px">Accusantium doloremque laudantium, totam rem aperiam, eaque ipsa quae ab illo inven tore veritatis et quasi architecto beatae vitae dicta sunt expli cabo nemo enim ipsam voluptatem quia voluptasea.</p>
  <div class="btn learn">LEARN MORE</div>
</section>

<!-- video + features -->
<svg class="abs feature-bg" width="1200" height="2342" viewBox="0 0 1200 2342">
  <polygon points="0,1662 1200,1392 1200,2342 0,2342" fill="#f2561d"/>
  <polygon points="0,1668 1200,1530 1200,2342 0,2342" fill="#141619"/>
</svg>
<div class="abs video-frame">
  <div class="video-art" role="img" aria-label="Illustration of relaxed coworkers chatting and lounging in armchairs in a break area"></div>
</div>
<svg class="abs" style="left:533px;top:1438px" width="134" height="134" viewBox="0 0 134 134">
  <circle cx="67" cy="67" r="64" fill="none" stroke="#fff" stroke-width="2.5"/>
  <circle cx="67" cy="67" r="44" fill="#fff"/>
  <polygon points="58,52 82,67 58,82" fill="#f2561d"/>
</svg>
<section class="features">
  <h2 class="abs serif">OUR FEATURES</h2>
  <p class="abs features-lead">Lorem ipsum dolor sit amet, consectetur adipiscing elit, sed do eiusmod tempor incididunt ut labore et dolore magna aliqua. Ut enim ad minim nostrud exeiscing do eiusmod tempor incididurcitationea.</p>

  <article class="feature-card" style="left:111px">
    <svg width="66" height="66" viewBox="0 0 66 66" fill="none" stroke="#f2561d" stroke-width="2.4">
      <circle cx="33" cy="33" r="22"/><circle cx="33" cy="33" r="29" stroke-dasharray="7 5"/>
      <circle cx="33" cy="27" r="6"/><path d="M22 44c2-6 6-8 11-8s9 2 11 8"/>
    </svg>
    <h3>WORK ENVIRONMENT<br>RIGHT NOW</h3>
    <p>Lorem ipsum dolor sit amet, consectetur adipiscing elit, sed do eiusmod tempor incididunt ut labore et dolore magna aliqu im ad minim veniamea.</p>
  </article>
  <article class="feature-card" style="left:446px">
    <svg width="66" height="66" viewBox="0 0 66 66" fill="none" stroke="#f2561d" stroke-width="2.4">
      <rect x="6" y="8" width="40" height="50" rx="3"/><rect x="13" y="16" width="8" height="7"/><path d="M26 19h14"/>
      <rect x="13" y="29" width="8" height="7"/><path d="M26 32h10"/><rect x="13" y="42" width="8" height="7"/><path d="M26 45h8"/>
      <circle cx="48" cy="36" r="10"/><path d="M55 43l8 9"/>
    </svg>
    <h3>PULSE<br>SURVEYS</h3>
    <p>Lorem ipsum dolor sit amet, consectetur adipiscing elit, sed do eiusmod tempor incididunt ut labore et dolore magna aliqu im ad minim veniamea.</p>
  </article>
  <article class="feature-card" style="left:779px">
    <svg width="66" height="66" viewBox="0 0 66 66" fill="none" stroke="#f2561d" stroke-width="2.4">
      <circle cx="33" cy="36" r="26"/><ellipse cx="33" cy="36" rx="11" ry="26"/><path d="M7 36h52M11 23h44M11 49h44M33 10v52"/>
      <rect x="26" y="4" width="14" height="18" fill="#fff"/><path d="M29 8h2M35 8h2M29 13h2M35 13h2M29 18h2M35 18h2"/>
    </svg>
    <h3>SYNCHRONIZE YOUR<br>ORGANIZATION</h3>
    <p>Lorem ipsum dolor sit amet, consectetur adipiscing elit, sed do eiusmod tempor incididunt ut labore et dolore magna aliqu im ad minim veniamea.</p>
  </article>
</section>

<!-- testimonials -->
<section class="testimonials">
  <h2 class="abs section-title serif" style="top:2420px">TESTIMONIALS</h2>
  <p class="quote-text" style="left:111px">Sed ut perspiciatis unde omnis iste natus error sit voluptatem acc usantium doloremque laudantium, totam rem aperiam, eaque ip sa quae ab illo inventciatis unde omnis iste natorea.</p>
  <div class="abs t-divider"></div>
  <p class="quote-text" style="left:649px">Sed ut perspiciatis unde omnis iste natus error sit voluptatem acc usantium doloremque laudantium, totam rem aperiam, eaque ip sa quae ab illo inventciatis unde omnis iste natorea.</p>

  <div class="avatar" style="left:111px" role="img" aria-label="Portrait of reviewer"></div>
  <div class="t-name" style="left:185px">Dana Whitcombe, <small>United States</small></div>
  <div class="stars" style="left:185px">★★★★★</div>
  <div class="qmark" style="left:495px">”</div>

  <div class="avatar" style="left:649px" role="img" aria-label="Portrait of reviewer"></div>
  <div class="t-name" style="left:723px">Dana Whitcombe, <small>United States</small></div>
  <div class="stars" style="left:723px">★★★★★</div>
  <div class="qmark" style="left:1033px">”</div>

  <div class="abs t-dots"><i></i><i class="on"></i><i></i><i></i></div>
</section>

<!-- trusted -->
<section class="abs trusted"></section>
<h2 class="abs section-title serif" style="top:2845px;color:#fff">TRUSTED BY</h2>
<svg class="arrow" style="left:46px" width="26" height="32" viewBox="0 0 26 32"><path d="M18 3L6 16l12 13" fill="none" stroke="#fff" stroke-width="5"/></svg>
<div class="partner" style="left:111px"><i></i></div>
<div class="partner" style="left:311px"><i></i></div>
<div class="partner" style="left:512px"><i></i></div>
<div class="partner" style="left:712px"><i></i></div>
<div class="partner" style="left:912px"><i></i></div>
<svg class="arrow" style="left:1127px" width="26" height="32" viewBox="0 0 26 32"><path d="M8 3l12 13L8 29" fill="none" stroke="#fff" stroke-width="5"/></svg>

<!-- blog -->
<section class="blog">
  <h2 class="abs section-title serif" style="top:3170px">LATEST <span class="accent">BLOG</span></h2>

  <article class="blog-card" style="left:111px">
    <div class="blog-img" role="img" aria-label="Team of coworkers smiling around a meeting table" style="background:linear-gradient(135deg,#c9ced4,#8c96a3 60%,#4d5665)"></div>
    <div class="blog-date"><svg width="14" height="14" viewBox="0 0 14 14"><rect x="1" y="2" width="12" height="11" rx="1" fill="none" stroke="#f2561d" stroke-width="1.6"/><path d="M1 6h12M4 0v4M10 0v4" stroke="#f2561d" stroke-width="1.6"/></svg>09 Mar 2022</div>
    <h3>LOREM IPSUM DOLOR SIT AMET CONSE CTETUREA</h3>
    <p>Sed ut perspiciatis unde omnis iste natus error sit voluptatem accusanti umea.</p>
    <div class="read">READ MORE <svg width="13" height="13" viewBox="0 0 13 13"><circle cx="6.5" cy="6.5" r="6.5" fill="#f2561d"/><path d="M5 3.5l3 3-3 3" fill="none" stroke="#fff" stroke-width="1.6"/></svg></div>
  </article>
  <article class="blog-card" style="left:446px">
    <div class="blog-img" role="img" aria-label="Business partners shaking hands in a modern office" style="background:linear-gradient(135deg,#dfe3e7,#9aa3ad 55%,#3f4652)"></div>
    <div class="blog-date"><svg width="14" height="14" viewBox="0 0 14 14"><rect x="1" y="2" width="12" height="11" rx="1" fill="none" stroke="#f2561d" stroke-width="1.6"/><path d="M1 6h12M4 0v4M10 0v4" stroke="#f2561d" stroke-width="1.6"/></svg>09 Mar 2022</div>
    <h3>LOREM IPSUM DOLOR SIT AMET CONSE CTETUREA</h3>
    <p>Sed ut perspiciatis unde omnis iste natus error sit voluptatem accusanti umea.</p>
    <div class="read">READ MORE <svg width="13" height="13" viewBox="0 0 13 13"><circle cx="6.5" cy="6.5" r="6.5" fill="#f2561d"/><path d="M5 3.5l3 3-3 3" fill="none" stroke="#fff" stroke-width="1.6"/></svg></div>
  </article>
  <article class="blog-card" style="left:779px">
    <div class="blog-img" role="img" aria-label="Colleagues reviewing work together on a laptop" style="background:linear-gradient(135deg,#e8ebee,#b5bcc4 55%,#6a7380)"></div>
    <div class="blog-date"><svg width="14" height="14" viewBox="0 0 14 14"><rect x="1" y="2" width="12" height="11" rx="1" fill="none" stroke="#f2561d" stroke-width="1.6"/><path d="M1 6h12M4 0v4M10 0v4" stroke="#f2561d" stroke-width="1.6"/></svg>09 Mar 2022</div>
    <h3>LOREM IPSUM DOLOR SIT AMET CONSE CTETUREA</h3>
    <p>Sed ut perspiciatis unde omnis iste natus error sit voluptatem accusanti umea.</p>
    <div class="read">READ MORE <svg width="13" height="13" viewBox="0 0 13 13"><circle cx="6.5" cy="6.5" r="6.5" fill="#f2561d"/><path d="M5 3.5l3 3-3 3" fill="none" stroke="#fff" stroke-width="1.6"/></svg></div>
  </article>
</section>

<!-- footer -->
<footer class="abs footer"></footer>
<div class="abs brand footer-brand">velrato</div>
<i class="f-social" style="left:152px"></i>
<i class="f-social" style="left:193px"></i>
<i class="f-social" style="left:233px"></i>
<i class="f-social" style="left:272px"></i>

<div class="f-head" style="left:433px">QUICK LINKS</div>
<div class="f-link" style="left:433px;top:3829px"><b></b>Home</div>
<div class="f-link" style="left:433px;top:3855px"><b></b>About</div>
<div class="f-link" style="left:433px;top:3881px"><b></b>Features</div>
<div class="f-link" style="left:433px;top:3907px"><b></b>Blog</div>
<div class="f-link" style="left:433px;top:3933px"><b></b>Contact</div>

<div class="f-head" style="left:646px">OTHER LINKS</div>
<div class="f-link" style="left:646px;top:3829px"><b></b>FAQ</div>
<div class="f-link" style="left:646px;top:3855px"><b></b>Privacy Policy</div>
<div class="f-link" style="left:646px;top:3881px"><b></b>Terms Of Use</div>
<div class="f-link" style="left:646px;top:3907px"><b></b>Legal Support</div>

<div class="f-head" style="left:867px">CONTACT INFO</div>
<div class="c-icon" style="top:3833px"><svg width="14" height="18" viewBox="0 0 14 18"><path d="M7 17s6-6.5 6-10.5A6 6 0 0 0 1 6.5C1 10.5 7 17 7 17z" fill="#fff"/><circle cx="7" cy="6.5" r="2.2" fill="#f2561d"/></svg></div>
<div class="c-text" style="top:3830px">28 Harwell Lane,<br>United States</div>
<div class="c-icon" style="top:3876px"><svg width="16" height="16" viewBox="0 0 16 16"><path d="M3.5 1l3 3-2 2c1 2 3.5 4.5 5.5 5.5l2-2 3 3-2 2.5C7 15 1 9 1 3.5z" fill="#fff"/></svg></div>
<div class="c-text" style="top:3882px">+1 (555) 214 7730</div>
<div class="c-icon" style="top:3918px"><svg width="16" height="12" viewBox="0 0 16 12"><rect width="16" height="12" rx="1.5" fill="#fff"/><path d="M1 1.5l7 5 7-5" fill="none" stroke="#f2561d" stroke-width="1.5"/></svg></div>
<div class="c-text" style="top:3924px">hello@velrato.io</div>

<div class="abs f-rule"></div>
<div class="abs copy">© 2022 Velrato &nbsp;|&nbsp; All Rights Reserved</div>

</body>
</html>
```